Flat bootstrap design for existing site

I'm looking for a modern flat design based around an existing logo. This has to be a custom design (no external templates), and implemented into a bootstrap framework.

The logo is attached as 2 versions - choose whichever you want, that flows better with whatever design you choose.

Added screenshots of the existing site (currently using the default bootstrap layouts). Please make your designs around those pages in the screenshots (i.e. the homepage only has the postal code input and the header). The active page has 3 screenshots, because I wanted to illustrate the other states that would be visible (in the table rows).

This is a moving/junk removal website, just for some context.

Here's some example websites (flat designs) that I like, just to give you an idea of what I'm after.

https://www.plimvora.com/
https://dacklow.com/
https://trevanu.com/
https://quobrintal.com/en/

Coding

Coded - Design and coding required

Number of Pages Required

5+ page

Colors

Designer to choose colors to be used in the design.

Requirements
Must have
• It must be a modern/simple flat design, that is built around the existing logo (attached).
• It has to be implemented using bootstrap.

```html
<!DOCTYPE html>
<html lang="en">
<head>
<meta charset="utf-8">
<title>KARVELO – Bookings</title>
<link href="https://fonts.googleapis.com/css2?family=Montserrat:wght@400;600;700;800&family=Roboto:wght@400;500&display=swap" rel="stylesheet">
<style>
:root{
  --sky:#38bdf0;
  --white:#ffffff;
  --ink:#3a3a4a;
  --title:#5b4fa8;
  --user:#4a3f9a;
  --btn:#0f85cc;
  --row-alt:#e3f1f9;
  --rule:#dcdfe3;
  --badge:#8dc63f;
  --band:#6a5acd;
  --social:#8e8bb8;
  --scene-a:#7fd3f5;
  --scene-b:#4aaee0;
}
*{box-sizing:border-box;margin:0;padding:0}
html,body{width:1200px;height:610px;overflow:hidden}
body{font-family:"Montserrat",sans-serif;background:var(--sky);position:relative;color:var(--ink)}
.site-header{position:absolute;left:144px;right:144px;top:0;height:80px}
.brand{position:absolute;left:0;top:22px;display:flex;align-items:center;gap:8px;color:var(--white);font-weight:800;font-size:30px;letter-spacing:1px}
.brand-dot{width:20px;height:20px;border-radius:50%;background:var(--white)}
.main-nav{position:absolute;right:0;top:22px;display:flex;align-items:center;height:35px}
.nav-link{color:var(--white);font-weight:700;font-size:11.5px;letter-spacing:.4px;text-decoration:none;margin-right:26px}
.nav-cta{background:var(--btn);color:var(--white);font-weight:700;font-size:11.5px;letter-spacing:.4px;height:35px;padding:0 12px;display:flex;align-items:center;border-radius:2px;margin-right:16px;margin-left:-2px}
.user-menu{display:flex;align-items:center;gap:6px;color:var(--user);font-size:12.5px;font-weight:600}
.user-icon{width:17px;height:17px;border-radius:50%;background:var(--user);display:flex;align-items:center;justify-content:center}
.bookings-card{position:absolute;left:144px;top:102px;width:912px;height:352px;background:var(--white);border-radius:3px;box-shadow:0 4px 14px rgba(0,60,110,.18);overflow:hidden}
.card-title{height:48px;border-bottom:1px solid var(--rule);padding:14px 15px 0;font-family:"Roboto",sans-serif;font-weight:500;font-size:19px;color:var(--title)}
.bookings-table{width:100%;border-collapse:collapse;margin-top:20px;table-layout:fixed}
.bookings-table th{font-family:"Roboto",sans-serif;font-weight:500;font-size:12.5px;color:#2b2b35;text-align:left;height:34px;vertical-align:bottom;padding:0 0 10px 15px;border-bottom:1px solid var(--rule)}
.bookings-table td{font-size:11.5px;height:41.6px;padding:0 0 0 15px;border-bottom:1px solid #eef0f2}
.bookings-table tbody tr:nth-child(odd){background:var(--row-alt)}
.col-id{width:144px}.col-date{width:202px}.col-desc{width:173px}.col-pack{width:144px}.col-time{width:142px}
.bookings-table .cell-status{text-align:right;padding:0 32px 0 0}
.status{display:inline-block;background:var(--badge);color:var(--white);font-size:10px;width:60px;height:18px;line-height:18px;text-align:center;border-radius:1px;vertical-align:middle}
.scene{position:absolute;left:1010px;top:385px;width:190px;height:161px;background:radial-gradient(ellipse at 80% 100%,var(--scene-a),var(--scene-b) 70%,transparent 71%)}
.site-footer{position:absolute;left:0;top:546px;width:1200px;height:58px;background:var(--white)}
.copyright{position:absolute;left:144px;top:24px;font-family:"Roboto",sans-serif;font-size:12px;color:#3e3a6a}
.social{position:absolute;left:987px;top:22px;display:flex;gap:6px}
.social span{width:19px;height:19px;background:var(--social);border-radius:2px}
.bottom-band{position:absolute;left:0;top:604px;width:1200px;height:6px;background:var(--band)}
</style>
</head>
<body>
<header class="site-header">
  <div class="brand"><span class="brand-dot"></span>KARVELO</div>
  <nav class="main-nav">
    <a class="nav-link" href="#">BOOK</a>
    <a class="nav-link" href="#">HOW IT WORKS</a>
    <span class="nav-cta">BECOME A DRIVER</span>
    <span class="user-menu">
      <span class="user-icon"><svg width="9" height="10" viewBox="0 0 9 10"><circle cx="4.5" cy="3" r="2.2" fill="none" stroke="#fff" stroke-width="1.2"/><path d="M1 9.5c0-2.2 1.6-3.4 3.5-3.4S8 7.3 8 9.5" fill="none" stroke="#fff" stroke-width="1.2"/></svg></span>
      quill@postbin.com
      <svg width="9" height="6" viewBox="0 0 9 6"><path d="M1 1l3.5 3.5L8 1" fill="none" stroke="#4a3f9a" stroke-width="1.5"/></svg>
    </span>
  </nav>
</header>

<section class="bookings-card">
  <h1 class="card-title">Bookings</h1>
  <table class="bookings-table">
    <thead>
      <tr><th class="col-id">Job Id</th><th class="col-date">Date Created</th><th class="col-desc">Description</th><th class="col-pack">Package</th><th class="col-time">Pick-up Time</th><th></th></tr>
    </thead>
    <tbody>
      <tr><td>4</td><td>July 13 at 5:42 pm</td><td>1 large thing</td><td>Package 1</td><td></td><td class="cell-status"><span class="status">Active</span></td></tr>
      <tr><td>3</td><td>July 13 at 5:42 pm</td><td>1 large thing</td><td>Package 2</td><td></td><td class="cell-status"><span class="status">Active</span></td></tr>
      <tr><td>2</td><td>July 13 at 5:42 pm</td><td>1 large thing</td><td>Package 1</td><td></td><td class="cell-status"><span class="status">Active</span></td></tr>
      <tr><td>1</td><td>July 13 at 5:42 pm</td><td>1 large thing</td><td>Package 2</td><td></td><td class="cell-status"><span class="status">Active</span></td></tr>
      <tr><td></td><td></td><td></td><td></td><td></td><td class="cell-status"></td></tr>
    </tbody>
  </table>
</section>

<div class="scene" role="img" aria-label="Illustration of a mover beside a bin, houses and a delivery van on a hill"></div>

<footer class="site-footer">
  <p class="copyright">© 2017 KARVELO. All rights reserved.</p>
  <div class="social"><span></span><span></span><span></span></div>
</footer>
<div class="bottom-band"></div>
</body>
</html>
```